Venture Capital Firm Needs Website Redesign

We need a bold revamp of our website (https://halverine.vc/)
which at the moment looks washed out. We want a crisp, fresh and unique look. Feel free to keep as much or as little content in the site. The only thing we need to keep is a team section. The site should convey a clear distinction between our 3 product lines: Venture Capital, Private Credit, and Crypto. Two versions of our logo are attached and they should not change. For design inspirations, we like http://www.9plm.com/ for a more simple site and for a more built out site we like http://bluetorch.com/

Updates
Industry/Entity Type
Investment
Coding
Coded - Design and coding required
Number of Pages Required
1 page
Font styles to use
Colors
Designer to choose colors to be used in the design.
Requirements
Must have
- - Clear distinction between our 3 product lines: Venture Capital, Private Credit
- - Team section

Nice to have
- Some really creative aspect like http://www.9plm.com/ has with the distinction between first, second, and third kind

```html
<!DOCTYPE html>
<html lang="en">
<head>
<meta charset="utf-8">
<title>Halverine</title>
<link href="https://fonts.googleapis.com/css2?family=Saira:wght@400;500;600&family=Arimo:wght@400;700&display=swap" rel="stylesheet">
<style>
:root{
  --olive:#7f9a5f;
  --olive-soft:#87a06a;
  --ink:#2b2b2b;
  --text:#444;
  --paper:#ffffff;
  --mist:#f2f3f5;
  --rule:#e3e3e3;
}
*{margin:0;padding:0;box-sizing:border-box}
html,body{width:738px;height:1200px;overflow:hidden;background:var(--paper)}
body{font-family:"Arimo",Arial,sans-serif;color:var(--text)}
.page{position:relative;width:738px;height:1200px;overflow:hidden}

.hero{position:absolute;left:0;top:0;width:738px;height:370px;
  background:linear-gradient(160deg,#4f6272 0%,#6c7f8e 35%,#8d9ba6 60%,#3d4b58 100%)}
.hero-photo{position:absolute;inset:0;
  background:radial-gradient(ellipse at 70% 40%,rgba(200,210,220,.35),rgba(40,52,64,.2) 60%,rgba(30,40,50,.45))}
.brand{position:absolute;left:60px;top:20px;display:flex;align-items:center;gap:6px;
  font-family:"Saira",sans-serif;font-weight:500;font-size:12px;letter-spacing:1px;color:#fff}
.brand-dot{width:12px;height:12px;border:1.5px solid #fff;border-radius:50%}
.nav{position:absolute;right:62px;top:20px;display:flex;gap:12px;
  font-family:"Saira",sans-serif;font-weight:600;font-size:10.5px;color:#fff}
.nav a{color:#fff;text-decoration:none;padding-bottom:2px}
.nav a.active{border-bottom:1.5px solid #fff}
.hero-title{position:absolute;left:0;width:738px;top:146px;text-align:center;
  font-family:"Saira",sans-serif;font-weight:500;font-size:22px;line-height:32px;color:#fff}
.btn{position:absolute;display:flex;align-items:center;justify-content:center;
  background:var(--olive);color:#fff;border-radius:14px;
  font-family:"Saira",sans-serif;font-weight:500;font-size:10.5px;text-decoration:none}
.hero .btn{left:309px;top:214px;width:120px;height:26px;letter-spacing:.5px}
.mouse{position:absolute;left:362px;top:291px}

.lines{position:absolute;left:69px;top:332px;width:601px;height:176px;background:var(--paper);display:flex}
.line{flex:1;text-align:center;position:relative;padding-top:14px}
.line + .line::before{content:"";position:absolute;left:0;top:18px;bottom:22px;width:1px;background:var(--rule)}
.line svg{display:block;margin:0 auto;height:54px}
.line h3{font-family:"Saira",sans-serif;font-weight:500;font-size:13px;color:var(--ink);margin-top:10px}
.line p{font-size:7px;line-height:12px;color:#444;width:130px;margin:8px auto 0}
.line a{display:inline-block;margin-top:7px;font-size:8px;color:#333}

.about{position:absolute;left:0;top:370px;width:738px;height:328px;background:var(--mist)}
.about h2{position:absolute;top:181px;width:738px;text-align:center;
  font-family:"Saira",sans-serif;font-weight:500;font-size:22px;color:var(--ink)}
.about p{position:absolute;top:222px;left:72px;width:594px;text-align:center;font-size:9.2px;line-height:17.3px;color:#444}

.team{position:absolute;left:0;top:698px;width:738px;height:306px;
  background:linear-gradient(90deg,#5a5a5a,#7a7a7a 30%,#686868 60%,#8a8a8a)}
.team-photo{position:absolute;inset:0;background:rgba(40,40,40,.35)}
.team h2{position:absolute;top:64px;width:738px;text-align:center;
  font-family:"Saira",sans-serif;font-weight:500;font-size:22px;color:#fff}
.team .lead{position:absolute;top:108px;width:738px;text-align:center;
  font-family:"Saira",sans-serif;font-weight:500;font-size:14.5px;line-height:22px;color:#fff}
.values{position:absolute;top:167px;width:738px;display:flex;justify-content:center;gap:22px;
  font-family:"Arimo",sans-serif;font-size:14px;color:#fff}
.team .btn{left:309px;top:209px;width:121px;height:26px}

.contact{position:absolute;left:0;top:1004px;width:738px;height:172px;background:var(--paper)}
.seal{position:absolute;left:198px;top:29px;width:122px;height:122px;border:2.5px solid var(--ink);border-radius:50%;
  display:flex;align-items:center;justify-content:center;
  font-family:"Saira",sans-serif;font-weight:500;font-size:15px;letter-spacing:1px;color:var(--ink)}
.info{position:absolute;left:341px;top:46px;font-family:"Saira",sans-serif;font-weight:500;font-size:13px;color:var(--ink)}
.info li{list-style:none;display:flex;gap:11px;align-items:flex-start;line-height:15px}
.info li + li{margin-top:10px}
.info svg{flex:none;width:18px;height:16px;margin-top:1px}

.footer{position:absolute;left:0;top:1176px;width:738px;height:24px;background:var(--olive-soft);
  text-align:center;line-height:24px;font-size:7.5px;color:#333}
</style>
</head>
<body>
<div class="page">

  <header class="hero">
    <div class="hero-photo" role="img" aria-label="Photograph of hands working with charts on paper and a laptop, overlaid with faint graph lines"></div>
    <div class="brand"><span class="brand-dot"></span>HALVERINE</div>
    <nav class="nav">
      <a class="active" href="#">Home</a><a href="#">Venture Capital</a><a href="#">Private Credit</a>
      <a href="#">Crypto</a><a href="#">Team</a><a href="#">Blog</a><a href="#">Contact Us</a>
    </nav>
    <h1 class="hero-title">Halverine Operates At The Intersection Of Technology<br>And Novel Asset Classes.</h1>
    <a class="btn" href="#">LEARN MORE</a>
    <svg class="mouse" width="14" height="22" viewBox="0 0 14 22"><rect x="1" y="1" width="12" height="20" rx="6" fill="none" stroke="#fff" stroke-width="1.3"/><line x1="7" y1="5" x2="7" y2="9" stroke="#fff" stroke-width="1.3"/></svg>
  </header>

  <section class="about">
    <h2>About Us</h2>
    <p>Halverine operates three businesses that bridge technology and finance. We invest in pre-seed venture capital, and build software for the companies we invest in. We manage direct private credit funds that provide private credit capital to alternative private credit platforms, enabling them to finance the loans they originate. We create crypto funds for individuals, IRAs and institutions to get simple and easy access to cryptocurrencies.</p>
  </section>

  <section class="lines">
    <div class="line">
      <svg viewBox="0 0 70 56" fill="none" stroke="#7f9a5f" stroke-width="2.2">
        <circle cx="38" cy="14" r="12"/><text x="38" y="19" font-size="13" fill="#7f9a5f" stroke="none" text-anchor="middle" font-family="Arimo, sans-serif">$</text>
        <rect x="6" y="34" width="8" height="18"/><path d="M14 38h18l6 4h-12M14 50h22l22-12c3-2 0-6-4-4l-14 6"/>
      </svg>
      <h3>Venture Capital</h3>
      <p>We invest in early-stage startups led by founders who are passionate and knowledgeable about the....[+]</p>
      <a href="#">Read More</a>
    </div>
    <div class="line">
      <svg viewBox="0 0 70 56" fill="none" stroke="#7f9a5f" stroke-width="2.4">
        <rect x="4" y="14" width="56" height="34" rx="4"/><path d="M14 8h50v32"/>
        <circle cx="18" cy="31" r="5"/><circle cx="26" cy="31" r="5"/><circle cx="46" cy="28" r="5"/><path d="M46 33v7M36 40h8"/>
      </svg>
      <h3>Private Credit</h3>
      <p>Halverine Private Credit provides capital to lending businesses that are focused on using technology...[+]t.</p>
      <a href="#">Read More</a>
    </div>
    <div class="line">
      <svg viewBox="0 0 70 56" fill="none" stroke="#7f9a5f" stroke-width="2.2">
        <circle cx="34" cy="30" r="14"/><circle cx="34" cy="30" r="9"/>
        <path d="M4 52l10-14 8 6M48 20l16-16M56 4h8v8"/><path d="M50 14v-8M55 12v-10M60 16v-6" stroke-width="1.6"/>
      </svg>
      <h3>Crypto</h3>
      <p>The Halverine Crypto Index tracks the top 15 cryptocurrencies weighted by market cap and rebalanced...[+]</p>
      <a href="#">Read More</a>
    </div>
  </section>

  <section class="team">
    <div class="team-photo" role="img" aria-label="Black and white grid of expressive team portrait photographs"></div>
    <h2>Our Team</h2>
    <p class="lead">Our Highly Skilled Financial Consultants Are People Who Personifies The<br>Very Qualities That Have Made Us Successful</p>
    <div class="values"><span>KNOWLEDGE.</span><span>EXPERIENCE.</span><span>ENTHUSIAM.</span><span>DEDICATION</span></div>
    <a class="btn" href="#">Read More About Us</a>
  </section>

  <section class="contact">
    <div class="seal">HALVERINE</div>
    <ul class="info">
      <li><svg viewBox="0 0 18 16" fill="none" stroke="#7f9a5f" stroke-width="1.3"><path d="M9 12s5-5 5-8a5 5 0 0 0-10 0c0 3 5 8 5 8z"/><circle cx="9" cy="4.5" r="1.8"/><path d="M2 15h14l-2-4M2 15l2-4"/></svg><span>218 Mercer Street, Suite 604<br>Northfield, NY 10417</span></li>
      <li><svg viewBox="0 0 18 16" fill="#7f9a5f"><rect x="2" y="4" width="14" height="9"/><path d="M2 4l7 5 7-5" stroke="#fff" stroke-width="1.2" fill="none"/></svg><span>info@halverine.vc</span></li>
      <li><svg viewBox="0 0 18 16" fill="none" stroke="#7f9a5f" stroke-width="1.4"><circle cx="9" cy="8" r="7"/><path d="M7 4c-2 2 0 7 4 8l1-2-2-1-1 1c-1-1-2-3-1-4l1-1-1-2z" fill="#7f9a5f" stroke="none"/></svg><span>321.654.0987</span></li>
    </ul>
  </section>

  <footer class="footer">Copyright © 2018 Halverine . All Rights Reserved</footer>
</div>
</body>
</html>
```